Website design with eCommerce for revolutionary new product in the manufacturing industry.

We need a website designed for a precision manufacturing company based in the suburbs of Minneapolis, Minnesota called Velkrin Manufacturing. We have a revolutionary new product, the TARN LOCK, to introduce and sell through an eCommerce storefront. The website would include company information, product information, and the storefront. Green is a color that represents Velkrin Manufacturing. The final design should communicate that we exclusively offer premium products at a premium price. The design should also let the customer know they are the focus of our work.

Target Market(s)

Machinists and machine shops

Industry/Entity Type

Manufacturing and machine shops

Coding

Coded - Design and coding required

Font styles to use
Sans Serif

Colors
59FF00
82FF00
B8FF75
E3FFCB
F4FFEA

Requirements
Must have
• eCommerce storefront, Made in USA references
Nice to have
• Home page, TARN LOCK Product page, About Us, Capabilities, Contact, etc.
Should not have
• Should not be too much text and reading.

```html
<!DOCTYPE html>
<html lang="en">
<head>
<meta charset="utf-8">
<title>TARN LOCK – Product</title>
<link href="https://fonts.googleapis.com/css2?family=Poppins:wght@400;500;600;700;800&display=swap" rel="stylesheet">
<style>
:root{
  --green:#59ff00;
  --green-2:#82ff00;
  --green-3:#b8ff75;
  --black:#0d0d0d;
  --dark:#161616;
  --white:#ffffff;
  --text:#222;
}
*{box-sizing:border-box;margin:0;padding:0}
html,body{width:1200px;height:2276px;overflow:hidden;background:var(--white);font-family:"Poppins",sans-serif;color:var(--text)}
.page{position:relative;width:1200px;height:2276px;overflow:hidden}

.site-header{position:absolute;top:0;left:0;width:1200px;height:44px;background:var(--black);display:flex;align-items:center;padding-left:40px;z-index:3}
.brand{display:flex;align-items:center;gap:8px;color:var(--white);font-weight:800;font-size:20px;letter-spacing:1px;white-space:nowrap}
.brand-dot{width:12px;height:12px;border-radius:50%;background:var(--green)}
.main-nav{margin-left:auto;display:flex;height:100%;align-items:center}
.main-nav a{color:var(--white);text-decoration:none;font-size:10px;font-weight:600;padding:0 12px;text-transform:uppercase;white-space:nowrap}
.main-nav a.cta{background:var(--green);color:var(--black);height:100%;display:flex;align-items:center;padding:0 22px}

.hero{position:absolute;top:44px;left:0;width:1200px;height:430px;background:radial-gradient(circle at 40% 35%,#5e5e5e,#2c2c2c 50%,#111 100%)}
.hero-title{position:absolute;top:150px;width:100%;text-align:center;color:var(--white);font-size:60px;font-weight:800;letter-spacing:2px}
.hero-slant{position:absolute;bottom:0;left:0}

.products{position:absolute;top:512px;left:0;width:1200px;display:flex;justify-content:center;gap:22px}
.product-card{width:258px;text-align:center}
.product-photo{position:relative;width:258px;height:250px;border-radius:4px;overflow:hidden;border:2px solid #2a2a2a;
  background:radial-gradient(ellipse at 30% 40%,#3b3b3b,#1d1d1d 70%)}
.product-photo::before{content:"";position:absolute;left:26%;top:18%;width:44%;height:18%;background:linear-gradient(135deg,#82ff00,#3aa800);border-radius:3px}
.product-photo::after{content:"";position:absolute;left:34%;top:34%;width:16%;height:46%;background:linear-gradient(180deg,#59ff00,#2f8f00);border-radius:3px}
.product-code{margin-top:92px;font-size:26px;font-weight:800;color:var(--black)}

.info-photo{position:absolute;left:60px;top:912px;width:540px;height:668px;border-radius:6px;
  background:radial-gradient(ellipse at 45% 45%,#82ff00 0%,#59ff00 30%,#e3ffcb 70%,#ffffff 100%)}
.info-body{position:absolute;left:620px;top:1036px;width:540px}
.info-title{display:flex;align-items:center;gap:12px;font-size:36px;font-weight:800;color:var(--black)}
.info-title::before{content:"";width:16px;height:16px;background:var(--green)}
.info-list{margin-top:22px;list-style:none;font-size:11.5px;line-height:1.55;color:#333}
.info-list li{position:relative;padding-left:16px}
.info-list li::before{content:"";position:absolute;left:2px;top:7px;width:6px;height:6px;border-radius:50%;background:var(--green)}
.info-list ul{list-style:none;padding-left:18px}
.info-list ul li::before{background:none;border:1px solid #777}

.footer{position:absolute;top:1620px;left:0;width:1200px;height:656px}
.footer-shape{position:absolute;top:0;left:0}
.footer-band{position:absolute;top:60px;left:0;width:1200px;height:120px;display:flex;align-items:center;padding:0 70px;color:var(--white)}
.footer-band .brand{font-size:28px}
.footer-band .divider{width:1px;height:50px;background:#555;margin:0 22px}
.tagline{font-size:12px;width:210px;line-height:1.5}
.call{margin-left:auto;display:flex;align-items:center;gap:10px;font-size:13px}
.call strong{font-size:30px;font-weight:700}
.call-icon{width:38px;height:38px;border-radius:50%;background:var(--green);display:flex;align-items:center;justify-content:center}
.footer-cols{position:absolute;top:300px;left:140px;display:flex;gap:80px;color:var(--white)}
.footer-col h4{font-size:17px;font-weight:700;margin-bottom:22px}
.footer-col a,.footer-col p{display:block;color:#ccc;font-size:11px;text-decoration:none;margin-bottom:8px}
.social{display:flex;align-items:center;gap:8px;margin-bottom:14px;font-size:11px;color:#ccc}
.social span{width:14px;height:14px;border-radius:3px;background:var(--green)}
.contact-item{margin-bottom:14px;font-size:11px;color:#ccc;line-height:1.5}
.contact-item b{color:var(--green);font-weight:600;display:block}
.field{width:210px;height:30px;border:1px solid #444;margin-bottom:8px;font-size:10px;color:#888;padding:8px 10px}
.submit{display:inline-block;background:var(--white);color:var(--black);font-weight:700;font-size:11px;padding:8px 14px;margin-top:4px}
.copyright{position:absolute;bottom:80px;width:100%;text-align:center;color:#888;font-size:10px}
.to-top{position:absolute;bottom:62px;right:44px;width:30px;height:30px;background:var(--green);display:flex;align-items:center;justify-content:center}
</style>
</head>
<body>
<div class="page">
  <header class="site-header">
    <div class="brand"><span class="brand-dot"></span>TARN LOCK</div>
    <nav class="main-nav">
      <a href="#">Why Velkrin Manufacturing?</a>
      <a href="#">What We Do</a>
      <a href="#">How We Make It Better</a>
      <a href="#">Capabilities</a>
      <a href="#">Gallery</a>
      <a href="#">About Us</a>
      <a href="#">Wisdom</a>
      <a href="#" class="cta">Contact</a>
    </nav>
  </header>

  <section class="hero" role="img" aria-label="Close-up photo of metal machining shavings">
    <h1 class="hero-title">PRODUCT</h1>
    <svg class="hero-slant" width="1200" height="100" viewBox="0 0 1200 100">
      <polygon points="0,100 1200,20 1200,100" fill="#ffffff"/>
      <polygon points="760,58 1200,20 1200,32 820,66" fill="#59ff00"/>
    </svg>
  </section>

  <section class="products">
    <div class="product-card"><div class="product-photo" role="img" aria-label="Green TARN LOCK stop TLK-001 in a foam case"></div><p class="product-code">TLK-001</p></div>
    <div class="product-card"><div class="product-photo" role="img" aria-label="Green TARN LOCK stop TLK-002 in a foam case"></div><p class="product-code">TLK-002</p></div>
    <div class="product-card"><div class="product-photo" role="img" aria-label="Green TARN LOCK stop TLK-003 in a foam case"></div><p class="product-code">TLK-003</p></div>
  </section>

  <div class="info-photo" role="img" aria-label="Large view of the green TARN LOCK machine stop with pins"></div>
  <section class="info-body">
    <h2 class="info-title">PRODUCT INFO</h2>
    <ul class="info-list">
      <li>Tooled and heat-treated steel body for lasting use</li>
      <li>The locking stop rail is the highest point, so cutting clearance is never an issue</li>
      <li>The stop rod is free-floating
        <ul><li>No need to slide it the full length to replace it</li></ul>
      </li>
      <li>You can use a wide range of shapes and sizes of stop rods
        <ul>
          <li>This means the end user can easily and quickly use</li>
          <li>almost any item at hand</li>
          <li>No need for exact shape and size rods</li>
        </ul>
      </li>
      <li>The clamping mechanisms do not require material deformation to function</li>
      <li>The adjustment fasteners are visible and easy to reach for quick and simple adjustments</li>
      <li>Only two fasteners are needed to access the full range of movements</li>
      <li>The arm can be rotated and adjusted without changing the X axis location</li>
      <li>The system can be mounted to many different vises, fixtures and pallet surfaces</li>
      <li>The design is modular to allow for easy customization or replacement of parts for shop and custom needs</li>
      <li>Inherently square to the workholding for intuitive adjustments</li>
      <li>Allows for use with very small, or very large parts, as well as oddly shaped parts</li>
      <li>Replacement parts are readily available</li>
      <li>The materials and fasteners are very common so maintenance is simple inside of one shop</li>
    </ul>
  </section>

  <footer class="footer">
    <svg class="footer-shape" width="1200" height="656" viewBox="0 0 1200 656">
      <polygon points="0,60 1200,0 1200,656 0,656" fill="#0d0d0d"/>
      <polygon points="700,34 1200,10 1200,60 840,78" fill="#59ff00"/>
      <polygon points="0,60 360,42 300,70 0,84" fill="#59ff00"/>
      <rect x="0" y="180" width="1200" height="476" fill="#161616"/>
    </svg>
    <div class="footer-band">
      <div class="brand"><span class="brand-dot"></span>TARN LOCK</div>
      <span class="divider"></span>
      <p class="tagline">Velkrin Manufacturing has humble roots, starting as many machine shops do</p>
      <div class="call">
        <span class="call-icon"><svg width="16" height="16" viewBox="0 0 24 24"><path d="M6.6 10.8a15 15 0 006.6 6.6l2.2-2.2a1 1 0 011-.25 11.4 11.4 0 003.6.6 1 1 0 011 1V20a1 1 0 01-1 1A17 17 0 013 4a1 1 0 011-1h3.5a1 1 0 011 1c0 1.25.2 2.45.6 3.6a1 1 0 01-.25 1z" fill="#0d0d0d"/></svg></span>
        Call us: <strong>+123 456 7890</strong>
      </div>
    </div>
    <div class="footer-cols">
      <div class="footer-col">
        <h4>Helpful Links</h4>
        <a href="#">Why Velkrin?</a><a href="#">What We Do</a><a href="#">How We Make It Better</a><a href="#">Capabilities</a><a href="#">Gallery</a><a href="#">About Us</a><a href="#">Wisdom</a><a href="#">Contact Us</a>
      </div>
      <div class="footer-col">
        <h4>Information</h4>
        <div class="social"><span></span>Community</div>
        <div class="social"><span></span>Updates</div>
        <div class="social"><span></span>Search</div>
        <div class="social"><span></span>Network</div>
        <div class="social"><span></span>Videos</div>
      </div>
      <div class="footer-col">
        <h4>Contact Us</h4>
        <div class="contact-item"><b>Email</b>info@tarnlock.com</div>
        <div class="contact-item"><b>Phone</b>+98 123 456 7890</div>
        <div class="contact-item"><b>Location</b>Some address line goes<br>here city name</div>
      </div>
      <div class="footer-col">
        <h4>Get In Touch</h4>
        <div class="field">Enter Name</div>
        <div class="field">Enter Company</div>
        <div class="field">Enter Country</div>
        <span class="submit">SUBMIT</span>
      </div>
    </div>
    <p class="copyright">©COPYRIGHT 2023 TARN LOCK. ALL RIGHTS RESERVED.</p>
    <span class="to-top"><svg width="12" height="12" viewBox="0 0 12 12"><path d="M2 8l4-4 4 4" stroke="#0d0d0d" stroke-width="2" fill="none"/></svg></span>
  </footer>
</div>
</body>
</html>
```